Nonprofit Marketing Service Postcard

I want an oversized postcard that can be sent to nonprofits that want marketing help using a program called velmor reach credits . The site www.fundharborly.example has more info. Nonrprofit can get $10,000 free advertising per month on velmor if they qualify. We help them qualify and stay qualified month after month and runtheir marketing campaign so it is effective

Went on vacation/holiday

Ideally postcard will be about 8.5 inches by 5.47 inches.

Target Market(s)

Midsized to large nonprofits looking for marketing help

Industry/Entity Type

Nonprofit marketing consulting

Requirements
Must have
• The ability to catch the eye and explain the value proposition
Nice to have
• similar to the website www.fundharborly.example

```html
<!DOCTYPE html>
<html lang="en">
<head>
<meta charset="utf-8">
<title>Fund Harborly Postcard</title>
<link href="https://fonts.googleapis.com/css2?family=Open+Sans:wght@400;600;700;800&family=Oswald:wght@500;700&display=swap" rel="stylesheet">
<style>
:root{
  --bg:#d9d9db;
  --blue:#2f4f9e;
  --blue-dark:#243d7d;
  --orange:#f08a1c;
  --ink:#2b2b2b;
  --muted:#6b6f78;
  --paper:#ffffff;
  --line:#c9ccd4;
}
*{box-sizing:border-box;margin:0;padding:0}
html,body{width:688px;height:1200px;overflow:hidden}
body{background:var(--bg);font-family:"Open Sans",Arial,sans-serif;color:var(--ink);position:relative}
.card{position:absolute;left:34px;width:620px;height:399px;background:var(--paper);overflow:hidden;box-shadow:0 4px 14px rgba(0,0,0,.18)}
.card--front{top:170px}
.card--back{top:630px}
.brand{display:flex;align-items:center;gap:6px;font-family:"Oswald",sans-serif;font-weight:700;font-size:20px;letter-spacing:1px;color:var(--blue);text-transform:uppercase}
.brand-mark{width:12px;height:12px;background:var(--orange)}

/* front */
.front-logo{position:absolute;left:18px;top:14px}
.hero-photo{position:absolute;left:262px;top:0;width:358px;height:176px;background:linear-gradient(135deg,#e9ecf2,#b9c2d3 55%,#8c95a8)}
.hero-panel{position:absolute;left:0;top:52px;width:262px;height:200px;background:var(--blue);color:#fff;padding:14px 16px}
.hero-kicker{font-size:9px;font-weight:700;color:var(--orange);text-transform:uppercase;letter-spacing:.5px}
.hero-title{font-family:"Oswald",sans-serif;font-weight:700;font-size:21px;line-height:1.12;text-transform:uppercase;margin-top:5px}
.hero-title em{font-style:normal;color:var(--orange)}
.hero-list{margin-top:9px;list-style:none;font-size:8px;line-height:1.5}
.hero-list li::before{content:"✓ ";color:var(--orange);font-weight:700}
.offer-band{position:absolute;left:262px;top:176px;width:358px;height:22px;background:var(--orange);color:#fff;font-size:9.5px;font-weight:700;display:flex;align-items:center;justify-content:center;text-transform:uppercase}
.features{position:absolute;left:270px;top:206px;width:342px;display:flex;justify-content:space-between}
.feature{width:106px;text-align:center;font-size:7px;line-height:1.4;color:var(--muted)}
.feature svg{display:block;margin:0 auto 3px}
.feature b{display:block;font-size:8px;color:var(--blue);text-transform:uppercase;margin-bottom:2px}
.front-body{position:absolute;left:16px;top:262px;width:590px;display:flex;gap:16px;font-size:7.5px;line-height:1.5;color:var(--muted)}
.front-body p{flex:1}
.front-body strong{color:var(--blue)}
.cta{position:absolute;left:16px;top:326px;font-size:10px;font-weight:800;color:var(--orange);text-transform:uppercase}
.contact-bar{position:absolute;left:0;bottom:0;width:100%;height:34px;background:var(--blue);color:#fff;display:flex;align-items:center;justify-content:space-around;font-size:10px;font-weight:600}
.contact-bar span{display:flex;align-items:center;gap:6px}

/* back */
.back-left{position:absolute;left:0;top:0;width:330px;height:365px;padding:14px 16px}
.back-head{background:var(--blue);color:#fff;font-family:"Oswald",sans-serif;font-weight:500;font-size:13px;text-transform:uppercase;padding:5px 10px;letter-spacing:.5px}
.back-lead{font-size:8px;line-height:1.5;color:var(--muted);margin:8px 0}
.back-cols{display:flex;gap:12px}
.back-col{flex:1}
.back-col h3{font-size:8.5px;font-weight:800;color:var(--orange);text-transform:uppercase;margin:6px 0 3px}
.back-col p{font-size:7px;line-height:1.5;color:var(--muted)}
.back-col ul{list-style:none;font-size:7px;line-height:1.55;color:var(--muted)}
.back-col li::before{content:"■ ";color:var(--blue);font-size:5px}
.divider{position:absolute;left:340px;top:20px;width:1px;height:325px;background:var(--line)}
.back-logo{position:absolute;left:356px;top:20px}
.stamp{position:absolute;right:18px;top:16px;width:56px;height:64px;border:1.5px dashed var(--line)}
.address{position:absolute;left:372px;top:200px;width:226px}
.address div{height:1px;background:var(--line);margin-bottom:24px}
.back-bar{position:absolute;left:0;bottom:0;width:100%;height:34px;background:var(--blue);color:#fff;display:flex;align-items:center;padding:0 18px;justify-content:space-between;font-size:9.5px;font-weight:600}
.back-bar .orange{color:var(--orange)}
</style>
</head>
<body>

<section class="card card--front">
  <div class="brand front-logo"><span class="brand-mark"></span>Fund Harborly</div>
  <div class="hero-photo" role="img" aria-label="Photo of a nonprofit team meeting around a table with laptops"></div>
  <div class="hero-panel">
    <div class="hero-kicker">Attention nonprofit leaders</div>
    <h1 class="hero-title">Get up to <em>$10,000</em> in free monthly advertising with velmor reach credits</h1>
    <ul class="hero-list">
      <li>We help your nonprofit qualify</li>
      <li>We keep you qualified month after month</li>
      <li>We run campaigns that bring real results</li>
    </ul>
  </div>
  <div class="offer-band">Free advertising for qualified nonprofits</div>
  <div class="features">
    <div class="feature">
      <svg width="22" height="22" viewBox="0 0 24 24" fill="none" stroke="#2f4f9e" stroke-width="2"><path d="M4 12l5 5L20 6"/></svg>
      <b>Qualify</b>Full help with the application steps
    </div>
    <div class="feature">
      <svg width="22" height="22" viewBox="0 0 24 24" fill="none" stroke="#2f4f9e" stroke-width="2"><circle cx="12" cy="12" r="9"/><path d="M12 7v5l3 3"/></svg>
      <b>Stay compliant</b>Monthly checks that keep your credits
    </div>
    <div class="feature">
      <svg width="22" height="22" viewBox="0 0 24 24" fill="none" stroke="#2f4f9e" stroke-width="2"><path d="M4 20V10M10 20V4M16 20v-8M22 20H2"/></svg>
      <b>Grow reach</b>Campaigns tuned for donors and volunteers
    </div>
  </div>
  <div class="front-body">
    <p><strong>Who we help:</strong> midsized to large nonprofits that want more visibility, more donors and more volunteers without adding staff.</p>
    <p><strong>What you get:</strong> a dedicated team that sets up, manages and reports on your velmor campaigns every single month.</p>
  </div>
  <div class="cta">Call today for a free consultation</div>
  <div class="contact-bar">
    <span><svg width="12" height="12" viewBox="0 0 24 24" fill="#fff"><path d="M6.6 10.8a15 15 0 006.6 6.6l2.2-2.2a1 1 0 011-.25 11.4 11.4 0 003.6.6 1 1 0 011 1V20a1 1 0 01-1 1A17 17 0 013 4a1 1 0 011-1h3.5a1 1 0 011 1 11.4 11.4 0 00.6 3.6 1 1 0 01-.25 1z"/></svg>(555) 014-2290</span>
    <span>www.fundharborly.example</span>
  </div>
</section>

<section class="card card--back">
  <div class="back-left">
    <div class="back-head">Who we are and what we do</div>
    <p class="back-lead">We are a nonprofit marketing team that turns velmor reach credits into steady traffic, new donors and lasting awareness for your cause.</p>
    <div class="back-cols">
      <div class="back-col">
        <h3>Getting qualified</h3>
        <p>We review your eligibility, prepare your account and guide you through each approval step.</p>
        <h3>Staying qualified</h3>
        <p>Credit rules change often. We track them and keep your account in good standing every month.</p>
      </div>
      <div class="back-col">
        <h3>Our services</h3>
        <ul>
          <li>Account setup and review</li>
          <li>Keyword research</li>
          <li>Ad writing and testing</li>
          <li>Landing page advice</li>
          <li>Monthly reporting</li>
        </ul>
        <h3>Why choose us</h3>
        <p>Focused only on nonprofits, with clear pricing and no long contracts.</p>
      </div>
    </div>
  </div>
  <div class="divider"></div>
  <div class="brand back-logo"><span class="brand-mark"></span>Fund Harborly</div>
  <div class="stamp"></div>
  <div class="address"><div></div><div></div><div></div><div></div></div>
  <div class="back-bar">
    <span>(555) 014-2290</span>
    <span class="orange">hello@fundharborly.example</span>
    <span>www.fundharborly.example</span>
  </div>
</section>

</body>
</html>
```